Webdesign für Kleingruppenreisen in die Südsteiermark
Zielgruppe
Wir sind ein Start-Up Unternehmen, das als Kleingruppenreisen in die Südsteiermark veranstaltet; der Schwerpunkt liegt auf dem Kulinarischen. Zielgruppe sind Geschäftsleute, die diese Kurzreisen (Do-So) für Marketingzwecke oder als Mitarbeiterbonus (oder auch privat) nutzen möchten.
Aufgabenstellung
Die Homepage soll eine Online-Shop Möglichkeit bieten, in der die Reise (bisher gibt es nur einen Ablauf) gebucht werden kann. Optisch sollte sie sich an das bereits von Ihnen erstellte Logo anlehnen und möglichst ansprechende Fotos von der Südsteiermark, Graz, Leoben usw. enthalten. (Siehe die beiden Flyer und das Logo)
Wir haben inzwischen Bildfreigaben von Haldauer und dem Tourismusverband Kellwinden erhalten und können auch eigene Bilder zur Verfügung stellen. Bitte kontaktieren Sie uns dafür, wenn nötig.

```html
<!DOCTYPE html>
<html lang="de">
<head>
<meta charset="utf-8">
<title>Gaumenfahrt – Genussreisen in die Steiermark</title>
<link rel="stylesheet" href="https://fonts.googleapis.com/css2?family=Montserrat:wght@300;400;500;600;700;800&family=Lora:wght@400&display=swap">
<style>
:root{
  --brown:#a97d5c;
  --brown-dark:#8e6446;
  --ink:#333333;
  --muted:#8a8a8a;
  --line:#e6e6e6;
  --panel:#efefef;
  --cream:#f7f6f3;
  --white:#ffffff;
  --green-dark:#3f6b1e;
  --green:#7fae3a;
  --wine:#6b1420;
}
*{box-sizing:border-box;margin:0;padding:0}
html,body{width:1200px;height:3255px;overflow:hidden}
body{font-family:"Montserrat",sans-serif;color:var(--ink);background:var(--white);position:relative}
.abs{position:absolute}

/* header */
.site-header{left:0;top:0;width:1200px;height:88px;background:var(--white);box-shadow:0 1px 4px rgba(0,0,0,.08);z-index:3}
.brand{left:63px;top:24px;display:flex;align-items:center;gap:8px;font-size:19px;font-weight:700;color:var(--brown-dark)}
.brand-dot{width:26px;height:26px;border-radius:50%;background:var(--brown)}
.main-nav{left:270px;top:46px;display:flex;gap:18px;font-size:15px;letter-spacing:4.5px;color:var(--brown);font-weight:500}
.main-nav span.sep{letter-spacing:0}

/* hero */
.hero{left:0;top:88px;width:1200px;height:587px;background:linear-gradient(180deg,#4d6a5c 0%,#8fb56a 28%,#7eaa39 55%,#4f7f22 80%,#2f5416 100%)}
.hero-title{left:0;top:238px;width:1220px;text-align:center;font-size:76px;font-weight:500;letter-spacing:5px;color:var(--white)}
.hero-rule{left:517px;top:350px;width:165px;height:1px;background:rgba(255,255,255,.8)}
.hero-text{left:380px;top:386px;width:440px;text-align:center;font-size:14.5px;line-height:18px;letter-spacing:1px;color:var(--white)}
.hero-btn{left:525px;top:499px;width:150px;height:33px;border:1px dashed rgba(255,255,255,.75);color:var(--white);font-size:10.5px;font-weight:700;letter-spacing:3px;display:flex;align-items:center;justify-content:center}
.hero-badge{left:562px;top:646px;width:76px;height:76px;border-radius:50%;background:var(--white);border:2px solid #e4d7cc;z-index:2;display:flex;align-items:center;justify-content:center}
.hero-badge i{width:40px;height:40px;border-radius:50%;border:2px solid var(--brown)}

/* about */
.about{left:0;top:675px;width:1200px;height:570px;background:var(--cream)}
.about-title{left:177px;top:742px;width:375px;text-align:center;font-size:38px;font-weight:400;color:#444}
.about-kicker{left:177px;top:792px;width:375px;text-align:center;font-size:10px;letter-spacing:1.4px;color:var(--brown)}
.about-copy{left:177px;top:830px;width:375px;text-align:center;font-size:11px;line-height:18px;letter-spacing:.9px;color:#444}
.about-copy p+p{margin-top:18px}
.photo{border:4px solid var(--white);outline:2px solid var(--green);outline-offset:-8px}
.tastes{left:758px;top:882px;width:160px;height:150px;border-radius:50%;background:var(--white);display:flex;align-items:center;justify-content:center;text-align:center;font-family:"Lora",serif;font-size:20px;letter-spacing:1.5px;line-height:27px;color:var(--brown)}

/* collections */
.collection-banner{left:126px;top:1245px;width:648px;height:388px;background:linear-gradient(160deg,#5f9a2a 0%,#8dbf4a 45%,#b89466 78%,#9c7a52 100%)}
.collection-title{left:178px;top:1345px;color:var(--white);font-weight:800;font-size:56px;line-height:58px}
.collection-title small{font-size:34px;font-weight:700}
.collection-sub{left:184px;top:1466px;color:var(--white);font-size:13px;font-weight:500}
.shop-now{left:184px;top:1512px;width:88px;height:30px;background:var(--brown);color:var(--white);font-size:9px;font-weight:700;letter-spacing:2px;display:flex;align-items:center;justify-content:center}
.feature-list{left:774px;top:1245px;width:298px;height:388px}
.feature{height:97px;background:var(--panel);border-bottom:1px solid #ddd;padding:0 30px;display:flex;align-items:center;font-size:13.5px;line-height:17px;color:#555;position:relative}
.feature.active{background:var(--brown);color:var(--white);overflow:visible}
.feature.active::before{content:"";position:absolute;left:-12px;top:36px;border-right:12px solid var(--brown);border-top:12px solid transparent;border-bottom:12px solid transparent}
.feature .num{position:absolute;left:82px;top:6px;font-size:80px;font-weight:700;color:rgba(255,255,255,.12)}
.wine-card{top:1633px;width:267px;height:182px;background:linear-gradient(180deg,#f2f2f2,#dcdcdc)}
.wine-card .cap{position:absolute;top:10px;width:100%;text-align:center;font-size:6.5px;font-weight:700;letter-spacing:1px;color:#555}
.wine-card .bottles{position:absolute;left:34px;top:34px;width:200px;height:112px;background:linear-gradient(90deg,#2a1a1a,#5a1a22,#2a1a1a,#3a2020)}

/* products */
.product-grid{left:128px;top:1897px;width:944px;height:304px;display:grid;grid-template-columns:repeat(4,1fr);border:1px solid var(--line)}
.product{border-right:1px solid var(--line);text-align:center;padding-top:26px;position:relative}
.product:last-child{border-right:none}
.product h3{font-size:14.5px;font-weight:500;line-height:18px;color:#444}
.product.active h3{color:var(--brown)}
.product .cat{font-size:9.5px;color:var(--muted);margin-top:10px}
.product .thumb{width:170px;height:170px;margin:14px auto 0;background:#e8e8e8}
.product.active .thumb{background:#f7f7f7}
.product .price{position:absolute;bottom:16px;width:100%;font-size:16px;color:var(--brown)}
.bag{position:absolute;left:66px;top:141px;width:106px;height:31px;background:var(--brown);color:var(--white);font-size:10px;font-weight:600;display:flex;align-items:center;justify-content:center}
.wish{position:absolute;top:190px;width:100%;font-size:10px;color:var(--muted)}
.mini-list{left:128px;top:2219px;width:460px;height:97px;border:1px solid var(--line);display:flex;align-items:center;padding-left:17px}
.mini-item{display:flex;align-items:center;gap:14px;width:226px}
.mini-item .sq{width:64px;height:64px;background:#e8e8e8}
.mini-item .cat{font-size:9px;color:var(--muted)}
.mini-item .name{font-size:13.5px;color:#444}
.mini-item .p{font-size:10.5px;color:var(--brown)}
.mini-item .p s{color:var(--muted);margin-right:4px}
.feature-item{left:613px;top:2219px;width:459px;height:97px;background:var(--panel);padding:18px 24px}
.feature-item .cat{font-size:9.5px;color:var(--brown);display:flex;align-items:center;gap:8px}
.feature-item .cat::before{content:"";width:16px;height:1px;background:var(--brown)}
.feature-item .name{font-size:17px;color:#444;margin-top:10px}
.feature-item .p{font-size:12px;color:var(--brown);margin-top:10px}

/* video */
.mill{left:562px;top:2392px;width:76px;height:70px;background:linear-gradient(180deg,#f0ebe6,#ddd1c6);border-radius:4px}
.video-title{left:0;top:2462px;width:1200px;text-align:center;font-size:38px;font-weight:500;color:#444}
.video-kicker{left:0;top:2511px;width:1200px;text-align:center;font-size:10px;letter-spacing:1.4px;color:var(--brown)}
.video{left:128px;top:2542px;width:944px;height:474px;background:radial-gradient(ellipse at 40% 35%,#e0d37a 0%,#a5a53a 35%,#5b6a22 65%,#3b2614 100%)}
.video-label{left:154px;top:2561px;color:var(--white);font-size:14px;font-weight:500}
.play{left:548px;top:2727px;width:104px;height:104px;border-radius:50%;border:2px solid var(--white)}
.controls{left:128px;top:2984px;width:944px;height:32px;background:rgba(0,0,0,.75)}
.progress{left:162px;top:2984px;width:125px;height:32px;background:var(--brown)}
.timecode{left:961px;top:2994px;font-size:11px;color:var(--white)}

/* contact */
.contact-col{top:3055px;width:300px;text-align:center}
.contact-col .label{font-size:15px;color:#444;margin-top:14px}
.contact-col .value{font-size:14px;color:#333;margin-top:16px;line-height:20px}
.contact-col .value.big{font-size:17px}
.contact-col .value.link{color:var(--brown)}
.site-footer{left:0;top:3202px;width:1200px;height:53px;border-top:1px solid var(--line);background:var(--white)}
.site-footer p{position:absolute;left:162px;top:22px;font-size:8.5px;color:#aaa}
</style>
</head>
<body>

<header class="site-header abs">
  <div class="brand abs"><span class="brand-dot"></span>Gaumenfahrt</div>
  <nav class="main-nav abs">
    <span>HOME</span><span class="sep">~</span><span>SERVICE</span><span class="sep">~</span><span>INFORMATIONEN</span><span class="sep">~</span><span>ONLINESHOP</span><span class="sep">~</span><span>CONTACT</span>
  </nav>
</header>

<section class="hero abs" role="img" aria-label="Foto: grüne Hügellandschaft der Steiermark mit Zypressen"></section>
<h1 class="hero-title abs">Gaumenfahrt</h1>
<div class="hero-rule abs"></div>
<p class="hero-text abs">Quisque rutrum. Aenean imperdiet. Etiam ultricies nisi vel augue. Curabitur ullamcorper ultricies nisi. Nam eget dui. Etiam rhoncus.</p>
<div class="hero-btn abs">ONLINESHOP</div>
<div class="hero-badge abs"><i></i></div>

<section class="about abs"></section>
<h2 class="about-title abs">Über uns</h2>
<p class="about-kicker abs">WE CREATE DELICIOUS MEMORIES</p>
<div class="about-copy abs">
  <p>Wir sind ein Start-up Unternehmen mit Sitz in Berlin und möchten unsere Begeisterung für die Steiermark mit ihren kulinarischen Spezialitäten, wunderschönen Landschaften und gastfreundlichen Menschen mit unseren Gästen teilen. Wir glauben, dass unsere Reisen hervorragende Möglichkeiten zum Entspannen und Genießen bieten und sich deshalb besonders gut als „Genussreise“ für umsatzstarke Kunden, erfolgreiche Mitarbeiter oder einfach als private Kurzreise mit Freunden eignen.</p>
  <p>Während Marketing und Vertrieb in Berlin angesiedelt sind, werden die Reisen selbst durch einen ortsansässigen Steirer durchgeführt. Dadurch können wir beste Qualität garantieren und auf Veränderungen flexibel reagieren. Unsere Partner sind ausgesuchte Hotels, Restaurants mit besonders guter Küche und Winzer der Spitzenklasse.</p>
  <p>Durch die kleine Gruppengröße von maximal 8 Personen können wir exklusiven Service bieten.</p>
</div>
<div class="photo abs" style="left:607px;top:764px;width:222px;height:188px;background:linear-gradient(160deg,#4e6e2c,#2c2a3c)" role="img" aria-label="Foto: dunkle Weintrauben am Rebstock"></div>
<div class="photo abs" style="left:843px;top:764px;width:222px;height:188px;background:linear-gradient(160deg,#8cbc4c,#5a8a26)" role="img" aria-label="Foto: zwei Gläser Rotwein im Grünen"></div>
<div class="photo abs" style="left:607px;top:966px;width:222px;height:188px;background:linear-gradient(160deg,#c9b3a6,#6b2430)" role="img" aria-label="Foto: Rotwein wird ins Glas gegossen"></div>
<div class="photo abs" style="left:843px;top:966px;width:222px;height:188px;background:linear-gradient(160deg,#6b8a2c,#c7cc6e)" role="img" aria-label="Foto: grüne Trauben am Weinstock"></div>
<div class="tastes abs">TASTES SO<br>GOOD!</div>

<div class="collection-banner abs" role="img" aria-label="Foto: zwei Rotweingläser und Trauben auf einem Holztisch"></div>
<div class="collection-title abs"><small>2018</small> New<br>Collections</div>
<p class="collection-sub abs">Your can put your own text here!</p>
<div class="shop-now abs">SHOP NOW</div>
<div class="feature-list abs">
  <div class="feature">The new collection of<br>best wine</div>
  <div class="feature active"><span class="num">02</span>2018 Collection<br>Your own text here!</div>
  <div class="feature">Sale of the day! Discounts<br>of 20 to 50% on all products</div>
  <div class="feature">New items of the summer<br>Your own text here</div>
</div>
<div class="wine-card abs" style="left:128px"><span class="cap">CHEAP SWEET RED WINES</span><div class="bottles" role="img" aria-label="Foto: vier Rotweinflaschen"></div></div>
<div class="wine-card abs" style="left:467px"><span class="cap">CHEAP SWEET RED WINES</span><div class="bottles" role="img" aria-label="Foto: vier Rotweinflaschen"></div></div>
<div class="wine-card abs" style="left:806px"><span class="cap">CHEAP SWEET RED WINES</span><div class="bottles" role="img" aria-label="Foto: vier Rotweinflaschen"></div></div>

<section class="product-grid abs">
  <article class="product"><h3>The Name of the<br>Wine</h3><p class="cat">Category</p><div class="thumb"></div><p class="price">$124</p></article>
  <article class="product active"><h3>The Name of the<br>Wine</h3><p class="cat">Category</p><div class="thumb"></div>
    <div class="bag">Add to Bag &nbsp;›</div><p class="wish">♥ &nbsp;Add to wishlist</p><p class="price">$76</p></article>
  <article class="product"><h3>The Name of the<br>Wine</h3><p class="cat">Category</p><div class="thumb"></div><p class="price">$92</p></article>
  <article class="product"><h3>The Name of the<br>Wine</h3><p class="cat">Category</p><div class="thumb"></div><p class="price">$117</p></article>
</section>
<div class="mini-list abs">
  <div class="mini-item"><div class="sq"></div><div><p class="cat">Category</p><p class="name">Red Wine</p><p class="p"><s>$83</s>$66</p></div></div>
  <div class="mini-item"><div class="sq"></div><div><p class="cat">Category</p><p class="name">White Wine</p><p class="p">$48</p></div></div>
</div>
<div class="feature-item abs"><p class="cat">Category</p><p class="name">The Name of the Wine</p><p class="p">$148</p></div>

<div class="mill abs" role="img" aria-label="Zeichnung: Windmühle"></div>
<h2 class="video-title abs">The Main Video Here</h2>
<p class="video-kicker abs">THE BEST WINE YOU'VE EVER TASTED!</p>
<div class="video abs" role="img" aria-label="Videobild: Rotweinflasche, zwei Gläser und Trauben auf einem Fass"></div>
<p class="video-label abs">Creative world space</p>
<svg class="play abs" viewBox="0 0 104 104" width="104" height="104"><polygon points="44,36 70,52 44,68" fill="#fff"/></svg>
<div class="controls abs"></div>
<div class="progress abs"></div>
<svg class="abs" style="left:138px;top:2993px" width="14" height="14" viewBox="0 0 14 14"><polygon points="3,2 12,7 3,12" fill="#fff"/></svg>
<span class="timecode abs">15:00</span>
<svg class="abs" style="left:1016px;top:2993px" width="14" height="14" viewBox="0 0 14 14"><polygon points="1,5 5,5 9,1 9,13 5,9 1,9" fill="#fff"/></svg>
<svg class="abs" style="left:1049px;top:2993px" width="14" height="14" viewBox="0 0 14 14" fill="none" stroke="#fff" stroke-width="2"><path d="M1 5V1h4M9 1h4v4M13 9v4H9M5 13H1V9"/></svg>

<div class="contact-col abs" style="left:146px">
  <svg width="26" height="42" viewBox="0 0 26 42" fill="none" stroke="#a97d5c" stroke-width="1.6"><rect x="2" y="2" width="22" height="38" rx="3"/><line x1="2" y1="8" x2="24" y2="8"/><line x1="2" y1="33" x2="24" y2="33"/></svg>
  <p class="label">Call us</p><p class="value big">+49 170 2837461</p>
</div>
<div class="contact-col abs" style="left:446px">
  <svg width="30" height="42" viewBox="0 0 30 42" fill="none" stroke="#a97d5c" stroke-width="1.6"><path d="M15 40C15 40 3 24 3 15a12 12 0 0 1 24 0c0 9-12 25-12 25z"/><circle cx="15" cy="15" r="5"/></svg>
  <p class="label">Location</p><p class="value">Gaumenfahrt Marlene Quast<br>Lindenhofweg 12, 10117 Berlin</p>
</div>
<div class="contact-col abs" style="left:753px">
  <svg width="44" height="42" viewBox="0 0 44 42" fill="none" stroke="#a97d5c" stroke-width="1.6"><rect x="2" y="10" width="40" height="28"/><path d="M2 10l20 16 20-16"/></svg>
  <p class="label">Mail</p><p class="value link">hallo@gaumenfahrt.de</p>
</div>

<footer class="site-footer abs"><p>All rights reserved</p></footer>

</body>
</html>
```